Wren Arts Competition Event For Teenagers Needs Promo Graphics

I am in need of graphics for 2019 Prairie Wren Arts Showcase. It is a Wren Arts competition event for teenagers. I need graphics to make an 11x17 poster and a main title graphic that I can use for digital (social, 16x9 for screens, etc). Graphic should include the following 2 logos: the KM Rising Tide logo (this is who we are) and the "circles" logo is the logo of Wren Arts Showcase so that can be incorporated but is not mandatory and does not need to be in color. Tag line for Wren Arts is "Discover. Develop. Deploy." Again, this is optional. Looking for an artistic design - geometric shapes, bright colors, or something along those lines. Something that speaks to teenagers and especially creatives/Wren Arts types. Additionally, Post should include:
Harbor Lane Chapel
March 29-30
(registration & cost info may be added to the poster before design is finalized; still working on those details)

```html
<!DOCTYPE html>
<html lang="en">
<head>
<meta charset="utf-8">
<title>2019 Prairie Wren Arts Showcase – Poster</title>
<link href="https://fonts.googleapis.com/css2?family=Archivo+Black&family=Archivo:wght@800&display=swap" rel="stylesheet">
<style>
  :root {
    --ink: #0a0a0a;
    --stage: #e9e7e4;
    --white: #ffffff;
    --pink: #ee5f8e;
    --hot-pink: #e8357a;
    --coral: #f0504a;
    --red-orange: #ee4b2b;
    --yellow: #f7c948;
    --sky: #8fd3ee;
    --lavender: #c9a3d6;
    --purple: #4a2a86;
    --brand-blue: #3fc3ee;
  }
  * { box-sizing: border-box; margin: 0; padding: 0; }
  html, body { width: 1200px; height: 756px; overflow: hidden; background: var(--stage); }
  .canvas { position: relative; width: 1200px; height: 756px; }
  .poster {
    position: absolute; left: 330px; top: 10px; width: 540px; height: 736px;
    overflow: hidden; background: var(--ink);
    font-family: "Archivo", "Arial Black", sans-serif; font-weight: 800;
  }

  .art-corner {
    position: absolute; right: 0; top: 0; width: 150px; height: 110px;
    background: linear-gradient(135deg, var(--yellow), var(--sky));
  }
  .title-sweep {
    position: absolute; left: 0; top: 150px; width: 540px; height: 170px;
    background: linear-gradient(90deg, var(--pink), var(--hot-pink));
    transform: skewY(-9deg); transform-origin: left top;
  }
  .art-field {
    position: absolute; left: 0; top: 380px; width: 300px; height: 356px;
    background: linear-gradient(160deg, var(--yellow) 0%, var(--pink) 35%, var(--coral) 65%, var(--sky) 100%);
  }
  .band-tagline {
    position: absolute; left: 300px; top: 452px; width: 240px; height: 110px;
    background: linear-gradient(90deg, var(--pink), var(--red-orange));
  }
  .band-dates {
    position: absolute; left: 300px; top: 562px; width: 240px; height: 94px;
    background: linear-gradient(90deg, var(--lavender), var(--sky));
  }

  .title { position: absolute; left: 34px; font-family: "Archivo Black", "Arial Black", sans-serif;
    color: var(--white); line-height: 1; letter-spacing: -0.5px;
    text-shadow: 3px 3px 0 var(--purple), 5px 5px 0 var(--hot-pink); }
  .title--year { top: 76px; font-size: 62px; }
  .title--main { top: 148px; font-size: 88px; }

  .title-band {
    position: absolute; left: 34px; top: 254px; width: 474px; height: 58px;
    background: linear-gradient(90deg, var(--pink), var(--hot-pink));
    display: flex; align-items: center; justify-content: center;
    font-family: "Archivo Black", "Arial Black", sans-serif; font-size: 33px;
    color: var(--ink); white-space: nowrap;
  }

  .mark-wren { position: absolute; left: 250px; top: 366px; width: 120px;
    font-size: 22px; line-height: 1.05; color: var(--white); text-align: center; }
  .mark-host { position: absolute; left: 384px; top: 366px; width: 140px;
    font-size: 22px; line-height: 1.05; color: var(--brand-blue); text-align: center; }

  .tagline { position: absolute; left: 348px; top: 462px; list-style: none;
    font-size: 26px; line-height: 30px; color: var(--ink); }
  .tagline li::before { content: "•"; color: var(--yellow); font-size: 18px; margin-right: 8px; vertical-align: 3px; }

  .dates { position: absolute; left: 360px; top: 576px; color: var(--ink); font-size: 26px; line-height: 1.1; }
  .dates__month { display: block; border-bottom: 3px solid var(--ink); padding-bottom: 2px; margin-bottom: 4px; width: 100px; }

  .venue { position: absolute; left: 152px; top: 516px; width: 196px; height: 196px; border-radius: 50%;
    background: linear-gradient(120deg, var(--pink), var(--lavender) 50%, var(--sky));
    display: flex; align-items: center; justify-content: center; text-align: center;
    font-size: 30px; line-height: 1.05; color: var(--ink); }
</style>
</head>
<body>
<div class="canvas">
  <section class="poster" aria-label="2019 Prairie Wren Arts Showcase poster">
    <div class="art-corner" role="img" aria-label="Geometric shapes in yellow and sky blue"></div>
    <div class="title-sweep"></div>
    <div class="art-field" role="img" aria-label="Geometric triangle pattern in yellow, pink, coral and sky blue"></div>
    <div class="band-tagline"></div>
    <div class="band-dates"></div>

    <h1 class="title title--year">2019</h1>
    <p class="title title--main">PRAIRIE</p>
    <p class="title-band">WREN ARTS SHOWCASE</p>

    <p class="mark-wren">WREN ARTS</p>
    <p class="mark-host">KM RISING TIDE</p>

    <ul class="tagline">
      <li>DISCOVER</li>
      <li>DEVELOP</li>
      <li>DEPLOY</li>
    </ul>

    <p class="dates"><span class="dates__month">MARCH</span>29–30</p>

    <p class="venue">HARBOR<br>LANE<br>CHAPEL</p>
  </section>
</div>
</body>
</html>
```